Business Card Design

I need business cards designed for a new company i have started that makes cakes, particularly themed kids cakes with a really modern design and I would like to have my business cards reflect this. I have attached some photos of cakes I have made and would like some to be used.

Industry/Entity Type

Business

Contact Information for Business Card

Business Name: Tarts and Treats by Maren
Mobile: 0492 815 063
email: maren@tartsandtreatsbymaren.example.au
Instagram: instagram.com/tartsandtreatsbymaren/
Facebook: fb.me/tartsandtreatsbymaren

Colors
e667a6
b768aa
3276b5

Requirements
Must have
• Business Name: Tarts and Treats by Maren
• Mobile: 0492 815 063
• email: maren@tartsandtreatsbymaren.example.au
• Instagram: instagram.com/tartsandtreatsbymaren/
• Facebook: fb.me/tartsandtreatsbymaren
Nice to have
• 2 to 3 pictures of my cakes

```html
<!DOCTYPE html>
<html lang="en">
<head>
<meta charset="utf-8">
<title>Tarts and Treats by Maren — Business Card</title>
<link href="https://fonts.googleapis.com/css2?family=Raleway:wght@300;400;600&display=swap" rel="stylesheet">
<style>
  :root {
    --pink: #e667a6;
    --pink-light: #f39ac6;
    --pink-deep: #d9559a;
    --purple: #b768aa;
    --purple-deep: #9a5a9c;
    --blue: #3276b5;
    --white: #ffffff;
    --cream: #fbf7fb;
    --backdrop: #ece6ea;
    --ink-soft: rgba(255,255,255,0.92);
  }
  * { box-sizing: border-box; margin: 0; padding: 0; }
  html, body {
    width: 1200px; height: 950px; overflow: hidden;
    background: var(--backdrop);
    font-family: "Raleway", Arial, sans-serif;
  }
  .canvas {
    position: relative; width: 1200px; height: 950px;
  }
  .card {
    position: absolute; left: 220px;
    width: 760px; height: 434px;
    border-radius: 6px; overflow: hidden;
    box-shadow: 0 10px 30px rgba(80,40,70,0.18);
  }
  .card--front {
    top: 30px;
    background: linear-gradient(160deg, var(--pink-light) 0%, var(--pink) 55%, var(--pink-deep) 100%);
  }
  .card--back { top: 490px; background: var(--white); }

  .front-band {
    position: absolute; top: 0; right: 0; width: 120px; height: 100%;
    background: linear-gradient(180deg, var(--purple) 0%, var(--purple-deep) 100%);
  }
  .brand-seal {
    position: absolute; border-radius: 50%;
    background: var(--cream);
    display: flex; align-items: center; justify-content: center;
    text-align: center;
  }
  .card--front .brand-seal {
    width: 380px; height: 380px; left: 345px; top: 10px;
    border: 6px solid var(--white);
  }
  .card--back .brand-seal {
    width: 230px; height: 230px; left: 265px; top: 102px;
    border: 4px solid var(--pink);
  }
  .brand-name {
    font-weight: 600; color: var(--purple);
    line-height: 1.1;
  }
  .card--front .brand-name { font-size: 46px; }
  .card--back .brand-name { font-size: 27px; }

  .contact {
    position: absolute; left: 44px; bottom: 40px;
    color: var(--ink-soft);
  }
  .contact__name {
    font-size: 19px; font-weight: 600; letter-spacing: 1.5px;
    text-transform: uppercase;
  }
  .contact__role {
    font-size: 13px; font-weight: 300; margin-top: 3px; margin-bottom: 14px;
  }
  .contact__list { list-style: none; }
  .contact__item {
    display: flex; align-items: center; gap: 10px;
    font-size: 13.5px; font-weight: 300; line-height: 24px;
  }
  .contact__icon {
    width: 14px; height: 14px; flex: none;
    display: flex; align-items: center; justify-content: center;
  }
  .contact__icon--square {
    background: var(--white); border-radius: 2px;
  }
</style>
</head>
<body>
<main class="canvas">

  <section class="card card--front" aria-label="Business card front">
    <div class="front-band"></div>
    <div class="brand-seal">
      <p class="brand-name">Tarts and<br>Treats<br>by Maren</p>
    </div>
    <div class="contact">
      <p class="contact__name">Rhea Calloway</p>
      <p class="contact__role">CEO/Founder</p>
      <ul class="contact__list">
        <li class="contact__item">
          <span class="contact__icon">
            <svg width="14" height="14" viewBox="0 0 24 24" aria-hidden="true">
              <rect x="6" y="1" width="12" height="22" rx="2.5" fill="none" stroke="#ffffff" stroke-width="2"/>
              <circle cx="12" cy="19" r="1.4" fill="#ffffff"/>
            </svg>
          </span>
          0492 815 063
        </li>
        <li class="contact__item">
          <span class="contact__icon contact__icon--square"></span>
          tartsandtreatsbymaren
        </li>
        <li class="contact__item">
          <span class="contact__icon contact__icon--square"></span>
          tartsandtreatsbymaren
        </li>
        <li class="contact__item">
          <span class="contact__icon">
            <svg width="14" height="14" viewBox="0 0 24 24" aria-hidden="true">
              <rect x="2" y="5" width="20" height="14" rx="1.5" fill="none" stroke="#ffffff" stroke-width="2"/>
              <path d="M3 6l9 7 9-7" fill="none" stroke="#ffffff" stroke-width="2"/>
            </svg>
          </span>
          maren@tartsandtreatsbymaren.example.au
        </li>
      </ul>
    </div>
  </section>

  <section class="card card--back" aria-label="Business card back">
    <div class="brand-seal">
      <p class="brand-name">Tarts and<br>Treats<br>by Maren</p>
    </div>
  </section>

</main>
</body>
</html>
```